Business Card Design - Amberfield Court

We are looking at a new design for our business cards that has a modern and professional look. We run a residential aged care facility focussing on the care of residents. The cards will be used for potential clients, consultants and business opportunities in this sector. Blue and white is our main colours and would to see these colours incorporated in the design.
Industry/Entity Type
Business
Contact Information for Business Card
Amberfield Court, Darren Walsh, dwalsh@amberfieldcourt.com.au, Finance Manager, 0472 639 208, BCom, 37 Marrabel Crescent, Brindle Vale, Qld 4093.
Look and feel
Each slider illustrates characteristics of the customer's brand and the style your logo design should communicate.

```html
<!DOCTYPE html>
<html lang="en">
<head>
<meta charset="utf-8">
<title>Amberfield Court – Business Card</title>
<link href="https://fonts.googleapis.com/css2?family=Source+Sans+3:wght@400;600&display=swap" rel="stylesheet">
<style>
  :root {
    --backdrop: #d8d3cb;
    --card: #ecebe8;
    --card-edge: #cfcbc4;
    --strip-tint: #c9c2b8;
    --name-band: #f4f3f0;
    --brand-ink: #2c3d4b;
    --panel-top: #2f5a70;
    --panel-bottom: #14374d;
    --name-ink: #f3d9c4;
    --body-ink: #e6ecef;
  }
  * { box-sizing: border-box; margin: 0; padding: 0; }
  html, body {
    width: 1200px;
    height: 969px;
    overflow: hidden;
    background: var(--backdrop);
    font-family: "Source Sans 3", "Myriad Pro", Arial, sans-serif;
  }
  .canvas {
    position: relative;
    width: 1200px;
    height: 969px;
  }
  .card {
    position: absolute;
    left: 368px;
    top: 75px;
    width: 464px;
    height: 820px;
    border-radius: 26px;
    background: var(--card);
    border: 1px solid var(--card-edge);
    box-shadow: 0 18px 40px rgba(0,0,0,0.12);
    overflow: hidden;
  }
  .column {
    position: absolute;
    left: 56px;
    width: 353px;
    top: 0;
    bottom: 0;
  }
  .column__strip {
    position: absolute;
    left: 0; right: 0; top: 0;
    height: 290px;
    background: linear-gradient(to bottom, var(--strip-tint), rgba(201,194,184,0.35));
  }
  .name-band {
    position: absolute;
    left: 0; right: 0;
    top: 290px;
    height: 56px;
    background: var(--name-band);
    display: flex;
    align-items: center;
    justify-content: center;
    gap: 12px;
  }
  .name-band__mark {
    width: 14px; height: 14px;
    border-radius: 50%;
    background: var(--brand-ink);
  }
  .name-band__text {
    font-weight: 600;
    font-size: 30px;
    letter-spacing: 1.5px;
    color: var(--brand-ink);
    text-transform: uppercase;
  }
  .details {
    position: absolute;
    left: 0; right: 0;
    top: 356px;
    bottom: 0;
    background: linear-gradient(to bottom, var(--panel-top), var(--panel-bottom));
    text-align: center;
    color: var(--body-ink);
  }
  .details__name {
    position: absolute; left: 0; right: 0;
    top: 104px;
    font-size: 27px;
    font-weight: 600;
    color: var(--name-ink);
  }
  .details__role {
    position: absolute; left: 0; right: 0;
    top: 139px;
    font-size: 20px;
    color: var(--name-ink);
  }
  .details__address {
    position: absolute; left: 0; right: 0;
    top: 228px;
    font-size: 20px;
    line-height: 29px;
  }
  .details__contact {
    position: absolute; left: 0; right: 0;
    top: 302px;
    font-size: 20px;
    line-height: 31px;
  }
</style>
</head>
<body>
  <main class="canvas">
    <article class="card" aria-label="Amberfield Court business card">
      <div class="column">
        <div class="column__strip"></div>
        <div class="name-band">
          <span class="name-band__mark"></span>
          <span class="name-band__text">Amberfield Court</span>
        </div>
        <section class="details">
          <p class="details__name">Darren Walsh BCom</p>
          <p class="details__role">Finance Manager</p>
          <p class="details__address">37 Marrabel Crescent<br>Brindle Vale, Qld 4093.</p>
          <p class="details__contact">Tel : 0472 639 208<br>dwalsh@amberfieldcourt.com.au<br>www.amberfieldcourt.com.au</p>
        </section>
      </div>
    </article>
  </main>
</body>
</html>
```